Life Coaching business needs a new flyer

We are an Australian business that specialises in Life Coaching, Career Coaching, Health and Wellness Coaching, Yoga and Pilates. We need a A4 double sided flyer that is full colour and folded to DL format. I have attached a couple of designs that I like and some pictures and would like the flyer to be bright yet stylish.

Industry/Entity Type

Life Coaching

```html
<!DOCTYPE html>
<html lang="en">
<head>
<meta charset="utf-8">
<title>Life Coaching Trifold Flyer</title>
<link rel="stylesheet" href="https://fonts.googleapis.com/css2?family=Source+Sans+3:ital,wght@0,400;0,600;0,700;1,700&display=swap">
<style>
  :root {
    --blue: #1f6db4;
    --blue-deep: #0f5aa6;
    --green: #5aab2b;
    --green-light: #8cc63f;
    --text: #5a5a5a;
    --paper: #ffffff;
    --mist: #e9f3fa;
  }
  * { margin: 0; padding: 0; box-sizing: border-box; }
  html, body { width: 1200px; height: 895px; overflow: hidden; background: var(--paper); }
  .flyer {
    position: relative;
    width: 1200px; height: 895px;
    font-family: "Source Sans 3", "Myriad Pro", Arial, sans-serif;
    color: var(--text);
    background: linear-gradient(180deg, var(--mist) 0%, #ffffff 45%, var(--mist) 100%);
  }
  .artwork { position: absolute; inset: 0; }
  .block { position: absolute; }
  .question-list { list-style: none; font-size: 14px; line-height: 18px; }
  .question-list li, .benefit-list li {
    position: relative; padding-left: 17px; margin-bottom: 4px;
  }
  .question-list li::before, .benefit-list li::before {
    content: "›";
    position: absolute; left: 0; top: 3px;
    width: 11px; height: 11px; border-radius: 50%;
    background: var(--green); color: #fff;
    font-size: 11px; line-height: 9px; text-align: center; font-weight: 700;
  }
  .tagline { font-size: 17px; font-weight: 700; font-style: italic; color: var(--green); }
  .section-title { font-size: 17px; font-weight: 700; color: var(--blue); line-height: 20px; margin-bottom: 2px; }
  .body-copy { font-size: 12.8px; line-height: 16px; text-align: justify; }
  .intro-copy { font-size: 13.5px; line-height: 18px; }
  .benefit-list { list-style: none; font-size: 13.5px; line-height: 14.7px; margin-top: 8px; }
  .right-copy p { font-size: 13.5px; line-height: 17px; margin-bottom: 6px; }
  .brand-name {
    position: absolute; left: 269px; top: 576px; width: 116px;
    text-align: center; font-size: 16px; font-weight: 700; color: var(--blue);
  }
</style>
</head>
<body>
<div class="flyer">
  <svg class="artwork" width="1200" height="895" viewBox="0 0 1200 895">
    <defs>
      <clipPath id="panel-left"><rect x="29" y="47" width="384" height="817"/></clipPath>
      <clipPath id="panel-middle"><rect x="413" y="47" width="376" height="817"/></clipPath>
      <linearGradient id="sea-sky" x1="0" y1="0" x2="0" y2="1">
        <stop offset="0" stop-color="#2f86cc"/>
        <stop offset="0.55" stop-color="#9fd0ef"/>
        <stop offset="1" stop-color="#2a7fc0"/>
      </linearGradient>
      <linearGradient id="pale-sky" x1="0" y1="0" x2="0" y2="1">
        <stop offset="0" stop-color="#cfe6f6"/>
        <stop offset="0.7" stop-color="#eef6fb"/>
        <stop offset="1" stop-color="#7fb7de"/>
      </linearGradient>
      <linearGradient id="lawn-sky" x1="0" y1="0" x2="0" y2="1">
        <stop offset="0" stop-color="#bfe0f4"/>
        <stop offset="0.5" stop-color="#d9ecf6"/>
        <stop offset="0.62" stop-color="#8ab85a"/>
        <stop offset="1" stop-color="#5e9a35"/>
      </linearGradient>
      <linearGradient id="beach-sky" x1="0" y1="0" x2="0" y2="1">
        <stop offset="0" stop-color="#9fcbe9"/>
        <stop offset="0.6" stop-color="#dcecf5"/>
        <stop offset="1" stop-color="#e8e2d4"/>
      </linearGradient>
    </defs>

    <rect x="29" y="180" width="384" height="460" fill="url(#sea-sky)" role="img" aria-label="Photo of a smiling senior couple sitting on the bow of a sailboat at sea"/>
    <rect x="413" y="47" width="376" height="240" fill="url(#pale-sky)" role="img" aria-label="Photo of a woman in a white outfit holding a balancing yoga pose by the sea"/>

    <g clip-path="url(#panel-left)">
      <path d="M29,47 H789 V157 C550,200 250,215 29,282 Z" fill="#ffffff"/>
      <path d="M0,614 C180,602 330,602 413,606 C550,613 680,626 789,640 V864 H0 Z" fill="#ffffff"/>
    </g>
    <g clip-path="url(#panel-middle)">
      <path d="M29,282 C250,215 550,200 789,157 V650 H29 Z" fill="#ffffff"/>
      <path d="M0,614 C180,602 330,602 413,606 C550,613 680,626 789,640 V864 H0 Z" fill="url(#lawn-sky)" role="img" aria-label="Photo of a group of people meditating cross-legged on grass by the water"/>
    </g>

    <path d="M29,282 C250,215 550,200 789,157" fill="none" stroke="var(--green-light)" stroke-width="12"/>
    <path d="M29,296 C250,229 550,214 789,171" fill="none" stroke="var(--blue)" stroke-width="3"/>
    <path d="M29,614 C180,602 330,602 413,606 C550,613 680,626 789,640" fill="none" stroke="var(--blue-deep)" stroke-width="7"/>
    <path d="M413,614 C550,621 680,634 789,648" fill="none" stroke="var(--green)" stroke-width="3"/>

    <path d="M789,350 C900,362 1050,380 1173,410 V560 C1050,585 900,620 789,652 Z" fill="url(#beach-sky)" role="img" aria-label="Photo of a man and a woman doing a tree yoga pose on a beach"/>
    <path d="M789,348 C900,360 1050,378 1173,408" fill="none" stroke="var(--blue-deep)" stroke-width="9"/>
    <path d="M789,650 C900,618 1050,583 1173,558" fill="none" stroke="var(--green-light)" stroke-width="10"/>
    <path d="M789,662 C900,630 1050,595 1173,570" fill="none" stroke="var(--blue)" stroke-width="3"/>

    <circle cx="327" cy="587" r="58" fill="#ffffff"/>
  </svg>

  <div class="brand-name">Serene Path</div>

  <ul class="block question-list" style="left:57px; top:78px; width:350px;">
    <li>Are you looking at making changes this year?</li>
    <li>Are you stuck in a rut or at a crossroad in your life?</li>
    <li>Are you wanting to lose weigh but can't get motivated?</li>
    <li>Do you have ongoing problems with your career, relationships, or just life itself?</li>
  </ul>
  <p class="block tagline" style="left:57px; top:196px;">Life coaching is the answer!</p>

  <div class="block" style="left:57px; top:683px; width:340px;">
    <h2 class="section-title">Life Coaching and Meditation<br>Centre of Excellence</h2>
    <p class="intro-copy" style="margin-top:6px;">Our mission is to help you become the best possible person you can be. Mentally, physically, and spiritually. We offer highly qualified and compassionate trainers/coaches for Life Coaching, Meditation, Yoga and Pilates.<br>They will guide and motivate you every step of the way to achieve all your dreams and goals. They will make you be the best you can be!</p>
  </div>

  <div class="block" style="left:430px; top:220px; width:348px;">
    <h2 class="section-title">Life Coaching</h2>
    <p class="body-copy">Your Life Coach will give you the confidence and the ability to move forward in a positive manner in all areas of your life where you crave change. Life Coaching is about breaking down the barriers preventing this change from happening, and creating the ideal environment for positive action to take place. It is a holistic approach, which looks at the present and sets goals for a totally successful future.</p>
  </div>
  <div class="block" style="left:430px; top:367px; width:348px;">
    <h2 class="section-title">Career Coaching</h2>
    <p class="body-copy">Are you at a crossroads in your career and at a loss about what to do next? Do you want your work to be in alignment with the authentic you? It can be difficult to assess career options, goals, and strategies, and have the confidence to implement changes on your own. With the right coaching support, you will gain the clarity that you need to take control and have a fulfilling and rewarding career.</p>
  </div>
  <div class="block" style="left:430px; top:512px; width:348px;">
    <h2 class="section-title">Wellness Coaching</h2>
    <p class="body-copy">Health and wellness coaches help their clients find the motivation and tools to achieve their health and wellness goals, working with the client to examine and improve the psychological framework that supports those goals.</p>
  </div>

  <div class="block right-copy" style="left:804px; top:76px; width:360px;">
    <h2 class="section-title">Why Would I Need Help?</h2>
    <p>Coaching is for anyone who wants to make lasting changes in their life.</p>
    <p>Coaching can assist with such issues as:</p>
    <ul class="benefit-list">
      <li>Creating a better work - life balance</li>
      <li>Resolving relationship issues</li>
      <li>Career guidance</li>
      <li>Stress management</li>
      <li>Weight loss and fitness</li>
      <li>Motivation and goal setting</li>
      <li>Boosting your self esteem</li>
      <li>Overcoming negative emotions and thoughts</li>
      <li>Better time management</li>
    </ul>
  </div>

  <div class="block" style="left:806px; top:695px; width:338px;">
    <h2 class="section-title">Meditation</h2>
    <p class="body-copy">We specialise in teaching meditation from beginners to advanced and teach a variety of techniques for stress reduction, peace of mind, stillness, and clarity.</p>
  </div>
  <div class="block" style="left:806px; top:770px; width:338px;">
    <h2 class="section-title">Yoga/Pilates</h2>
    <p class="body-copy">Your highly qualified and experienced Yoga or Pilates instructor will come to you and create a fun and varied workout based on what you enjoy and what your goals are.</p>
  </div>
</div>
</body>
</html>
```